New Innovative Counselling and psychotherapy Service needs Business Card design

Keep it simple and professional. On one side, just company name and logo (perhaps in all blue) and maybe a tag line.

On other side (all white) my name and Qualifications in centre

Industry/Entity Type

Health And Wellness

Contact Information for Business Card

Dara Whelby
Counsellor & Psychotherapist
BSc (Psychol.), BA, Dip. (Couns. & Psych.), PG.Cert (CBT), FGTrK, ONRE

I will also require Mobile no, Email and web site address of which I'll pass on to final designer.

Font styles to use
Sans Serif

Requirements
Must have
• My Logo Only and please use the colours in logo that is in it.
Should not have
• Any other images

```html
<!DOCTYPE html>
<html lang="en">
<head>
<meta charset="utf-8">
<title>Stillwater Lane – Business Card</title>
<link href="https://fonts.googleapis.com/css2?family=Open+Sans:wght@300;400;600;700&display=swap" rel="stylesheet">
<style>
  :root{
    --bg:#e9e7e3;
    --card-white:#ffffff;
    --card-dark:#333333;
    --brand-blue:#42aee8;
    --brand-green:#8cc63f;
    --ink:#3d3d3d;
    --ink-soft:#6b6b6b;
    --rule:#cfcfcf;
  }
  *{margin:0;padding:0;box-sizing:border-box}
  html,body{width:1200px;height:950px;overflow:hidden;background:var(--bg);font-family:"Open Sans",Arial,sans-serif}
  .canvas{position:relative;width:1200px;height:950px}

  .card{position:absolute;width:700px;height:400px;border-radius:22px;overflow:hidden;box-shadow:0 10px 28px rgba(0,0,0,.18)}
  .card--front{left:60px;top:50px;background:var(--card-white)}
  .card--back{left:440px;top:500px;background:var(--card-dark)}

  /* front */
  .brand{position:absolute;left:42px;top:156px;display:flex;align-items:center;gap:12px}
  .brand__dot{width:34px;height:34px;border-radius:50%;background:var(--brand-blue)}
  .brand__name{font-weight:300;font-size:28px;color:var(--ink-soft);letter-spacing:-.2px;white-space:nowrap}

  .divider{position:absolute;left:330px;top:60px;width:1px;height:200px;background:var(--rule)}

  .details{position:absolute;left:356px;top:52px;right:24px}
  .details__name{font-weight:700;font-size:30px;color:var(--brand-blue);line-height:1.1}
  .details__role{font-weight:400;font-size:18px;color:var(--brand-green);margin-top:6px}
  .details__quals{font-weight:400;font-size:13px;color:var(--brand-green);line-height:1.45;margin-top:4px}

  .contacts{list-style:none;margin-top:24px}
  .contacts li{display:flex;align-items:center;gap:10px;font-size:15px;color:var(--ink);line-height:1.65}
  .contacts svg{width:14px;height:14px;flex:none}

  .tag-band{position:absolute;left:0;right:0;bottom:0;height:54px;background:var(--brand-blue);border-top:5px solid var(--brand-green);box-shadow:inset 0 4px 0 var(--card-white)}
  .tag-band__text{position:absolute;left:0;right:0;top:14px;text-align:center;color:var(--card-white);font-size:17px;font-weight:400;letter-spacing:.2px;white-space:nowrap}

  /* back */
  .back-brand{position:absolute;inset:0;display:flex;align-items:center;justify-content:center;gap:18px}
  .back-brand__dot{width:52px;height:52px;border-radius:50%;background:var(--brand-blue)}
  .back-brand__name{font-weight:600;font-size:40px;color:var(--brand-blue)}
</style>
</head>
<body>
<main class="canvas">

  <section class="card card--front" aria-label="Business card front">
    <div class="brand">
      <span class="brand__dot"></span>
      <span class="brand__name">Stillwater Lane</span>
    </div>

    <div class="divider"></div>

    <div class="details">
      <h1 class="details__name">Dara Whelby</h1>
      <p class="details__role">Counsellor &amp; Psychotherapist</p>
      <p class="details__quals">MSc (Couns.), BA, Dip. (Family Therapy)<br>Cert. (Mindfulness), FGTrK.</p>

      <ul class="contacts">
        <li>
          <svg viewBox="0 0 14 14"><rect x="1.5" y="1.5" width="11" height="11" rx="1.5" fill="none" stroke="var(--brand-blue)" stroke-width="2"/></svg>
          555 214 7083
        </li>
        <li>
          <svg viewBox="0 0 14 14"><rect x="1" y="3" width="12" height="8" fill="var(--brand-blue)"/><path d="M1 3l6 4.5L13 3" fill="none" stroke="#fff" stroke-width="1.2"/></svg>
          dara@stillwaterlane.com
        </li>
        <li>
          <svg viewBox="0 0 14 14"><circle cx="7" cy="7" r="6" fill="var(--brand-blue)"/><path d="M1 7h12M7 1c-3 3-3 9 0 12M7 1c3 3 3 9 0 12" fill="none" stroke="#fff" stroke-width="1"/></svg>
          www.stillwaterlane.com
        </li>
      </ul>
    </div>

    <div class="tag-band">
      <p class="tag-band__text">Supporting Your Mind With Warmth, Patience And Quiet Respect</p>
    </div>
  </section>

  <section class="card card--back" aria-label="Business card back">
    <div class="back-brand">
      <span class="back-brand__dot"></span>
      <span class="back-brand__name">Stillwater Lane</span>
    </div>
  </section>

</main>
</body>
</html>
```